business card deign

Logo needs the following on it.
1. attached logo
2. Tagline - "If it keeps a drink cold or the party going...we do it!"
3. Name- Dalton Pikes, Founder and CPO
4. Address - 412 E. Carver Avenue, Ste 2207, Tampa, FL. 33917
5. Phone - 555.318.4726

```html
<!DOCTYPE html>
<html lang="en">
<head>
<meta charset="utf-8">
<title>Coolvane Business Card</title>
<link href="https://fonts.googleapis.com/css2?family=Arimo:wght@400;700&display=swap" rel="stylesheet">
<style>
  :root {
    --backdrop: #3d3d3d;
    --card-light: #ffffff;
    --card-dark: #2f2f2f;
    --ink: #1a1a1a;
    --ink-soft: #555555;
    --rule: #c9c9c9;
    --paper-text: #f4f4f4;
  }
  * { margin: 0; padding: 0; box-sizing: border-box; }
  html, body {
    width: 1200px; height: 803px; overflow: hidden;
    background: var(--backdrop);
    font-family: "Arimo", Arial, sans-serif;
  }
  .stage {
    width: 1200px; height: 803px;
    display: flex; align-items: center; justify-content: center; gap: 60px;
  }
  .card {
    width: 500px; height: 286px; border-radius: 22px;
    position: relative; overflow: hidden;
    box-shadow: 0 14px 30px rgba(0,0,0,0.35);
  }
  .card-front { background: var(--card-light); color: var(--ink); }
  .card-back { background: var(--card-dark); color: var(--paper-text); }

  .front-brand {
    position: absolute; top: 34px; right: 40px;
    display: flex; align-items: center; gap: 10px;
  }
  .brand-dot { width: 14px; height: 14px; border-radius: 50%; background: var(--ink); }
  .brand-name {
    font-weight: 700; font-size: 22px; letter-spacing: 7px; color: var(--ink);
  }
  .front-rule {
    position: absolute; left: 40px; right: 40px; top: 96px;
    height: 1px; background: var(--rule);
  }
  .front-address {
    position: absolute; top: 108px; right: 40px; text-align: right;
    font-size: 12px; line-height: 17px; color: var(--ink);
  }
  .front-person { position: absolute; left: 40px; bottom: 30px; }
  .person-name { font-weight: 700; font-size: 19px; text-transform: uppercase; letter-spacing: 0.3px; }
  .person-title { font-size: 12px; color: var(--ink-soft); margin-top: 2px; }
  .person-rule { width: 170px; height: 1px; background: var(--rule); margin: 9px 0 7px; }
  .contact-list { list-style: none; font-size: 12.5px; line-height: 17px; }
  .contact-list li { display: flex; align-items: center; gap: 7px; }
  .contact-list svg { width: 10px; height: 10px; fill: var(--ink); flex: none; }

  .back-content {
    position: absolute; inset: 0;
    display: flex; flex-direction: column; align-items: center; justify-content: center;
  }
  .back-brand { display: flex; align-items: center; gap: 14px; }
  .back-brand .brand-dot { background: var(--paper-text); width: 18px; height: 18px; }
  .back-brand .brand-name { color: var(--paper-text); font-size: 32px; letter-spacing: 11px; }
  .back-url { margin-top: 26px; font-size: 13px; letter-spacing: 3px; color: var(--paper-text); }
</style>
</head>
<body>
<main class="stage">
  <section class="card card-front">
    <div class="front-brand">
      <span class="brand-dot"></span>
      <span class="brand-name">COOLVANE</span>
    </div>
    <div class="front-rule"></div>
    <address class="front-address" style="font-style:normal">
      412 E. Carver Avenue<br>Ste 2207<br>Tampa, FL. 33917
    </address>
    <div class="front-person">
      <p class="person-name">Dalton Pikes</p>
      <p class="person-title">Founder and CPO</p>
      <div class="person-rule"></div>
      <ul class="contact-list">
        <li><svg viewBox="0 0 10 10"><path d="M2 0.5 L3.6 2.6 L2.7 3.6 Q3.8 5.9 6.3 7.2 L7.3 6.3 L9.5 7.8 L8.6 9.5 Q3.5 9 0.5 2 Z"/></svg>555.318.4726</li>
        <li><svg viewBox="0 0 10 10"><path d="M0.5 2 H9.5 V8 H0.5 Z M1.2 2.6 L5 5.4 L8.8 2.6 V2.8 L5 5.8 L1.2 2.8 Z" fill-rule="evenodd"/></svg>info@coolvane.com</li>
        <li><svg viewBox="0 0 10 10"><circle cx="5" cy="5" r="4.5"/></svg>www.coolvane.com</li>
      </ul>
    </div>
  </section>

  <section class="card card-back">
    <div class="back-content">
      <div class="back-brand">
        <span class="brand-dot"></span>
        <span class="brand-name">COOLVANE</span>
      </div>
      <p class="back-url">www.coolvane.com</p>
    </div>
  </section>
</main>
</body>
</html>
```